Business Card Design Project

This is the first time we use our new logo. We need a business card that we can use both on our institutional corporate relationships and also that works for our staff that deals with consumers directly.

VELUNDA is a new company dedicated to empower consumers and to provide them with the best choices for specialized health care using the latest telemedicine technology (medicine at a distance via videoconference).

We want to print this cards in high quality materials and process. We will like designs that allow us to use UV spot varnish and other techniques that will differentiate us.

We are including Two different versions of Color logos. In addition we are including white over black background logos. Those can be used replacing the black for a color.

Please note this is the first time we will be creating any corporate materials with our new logo and colors.

Target Market(s)

34+ consumers of medium high and high socioeconomic levels.

Industry/Entity Type

Health

Requirements
Must have
• Our logo on its original colors
Should not have
• Any other graphical element or design that is not our logo

```html
<!DOCTYPE html>
<html lang="en">
<head>
<meta charset="utf-8">
<title>VELUNDA Business Card</title>
<link rel="stylesheet" href="https://fonts.googleapis.com/css2?family=Montserrat:wght@600;700&family=Arimo:wght@400;700&display=swap">
<style>
  :root {
    --page-bg: #e9e9ee;
    --card-white: #ffffff;
    --sky-blue: #58b4dd;
    --deep-blue: #1d5b8a;
    --ribbon-blue: #1f6fb8;
    --ink: #1c1c1c;
    --divider: #c9c9c9;
  }
  * { margin: 0; padding: 0; box-sizing: border-box; }
  html, body { width: 1200px; height: 987px; overflow: hidden; }
  body {
    background: var(--page-bg);
    position: relative;
    font-family: "Arimo", Arial, sans-serif;
  }
  .card {
    position: absolute;
    width: 620px;
    height: 354px;
    border-radius: 30px;
    overflow: hidden;
  }
  /* Back side */
  .card-back {
    left: 540px;
    top: 80px;
    background: var(--sky-blue);
  }
  .back-brand {
    position: absolute;
    left: 0; right: 0;
    top: 110px;
    display: flex;
    justify-content: center;
    align-items: center;
    gap: 18px;
  }
  .back-brand .mark-dot {
    width: 34px; height: 34px;
    border-radius: 50%;
    background: var(--card-white);
  }
  .back-brand .brand-name {
    font-family: "Montserrat", Arial, sans-serif;
    font-weight: 700;
    font-size: 62px;
    letter-spacing: 4px;
    color: var(--card-white);
  }
  .back-url {
    position: absolute;
    left: 0; right: 0;
    top: 220px;
    text-align: center;
    color: var(--card-white);
    font-size: 20px;
    letter-spacing: 7px;
  }
  /* Front side */
  .card-front {
    left: 60px;
    top: 530px;
    background: var(--card-white);
  }
  .front-swoosh { position: absolute; inset: 0; }
  .front-brand {
    position: absolute;
    left: 150px;
    top: 56px;
    display: flex;
    align-items: center;
    gap: 16px;
  }
  .front-brand .mark-dot {
    width: 40px; height: 40px;
    border-radius: 50%;
    background: var(--sky-blue);
  }
  .front-brand .brand-name {
    font-family: "Montserrat", Arial, sans-serif;
    font-weight: 700;
    font-size: 58px;
    letter-spacing: 3px;
    color: var(--deep-blue);
  }
  .address {
    position: absolute;
    left: 130px;
    top: 160px;
    width: 170px;
    text-align: right;
    font-size: 17px;
    line-height: 24px;
    color: var(--ink);
  }
  .divider {
    position: absolute;
    left: 318px;
    top: 156px;
    width: 1px;
    height: 84px;
    background: var(--divider);
  }
  .contacts {
    position: absolute;
    left: 336px;
    top: 156px;
    list-style: none;
    font-size: 18px;
    line-height: 26px;
    color: var(--ink);
  }
  .contacts li { display: flex; align-items: center; gap: 8px; }
  .contacts svg { width: 14px; height: 14px; flex: none; }
  .holder {
    position: absolute;
    left: 36px;
    bottom: 26px;
    color: var(--card-white);
    font-size: 28px;
  }
  .holder strong { font-weight: 700; }
  .holder span { font-size: 22px; }
</style>
</head>
<body>
  <section class="card card-back" aria-label="Card back">
    <div class="back-brand">
      <div class="mark-dot"></div>
      <div class="brand-name">VELUNDA</div>
    </div>
    <div class="back-url">www.velunda.com</div>
  </section>

  <section class="card card-front" aria-label="Card front">
    <svg class="front-swoosh" viewBox="0 0 620 354" preserveAspectRatio="none" aria-hidden="true">
      <path d="M0,150 Q150,300 620,354 L0,354 Z" fill="var(--sky-blue)"/>
      <path d="M0,132 Q140,292 560,345" fill="none" stroke="var(--ribbon-blue)" stroke-width="6"/>
    </svg>

    <div class="front-brand">
      <div class="mark-dot"></div>
      <div class="brand-name">VELUNDA</div>
    </div>

    <div class="address">
      Street Name<br>City Name<br>State, City Zip Code
    </div>
    <div class="divider"></div>
    <ul class="contacts">
      <li><svg viewBox="0 0 16 16"><path d="M4 1 L6 5 L4.5 6.5 Q6 10 9.5 11.5 L11 10 L15 12 L13.5 15 Q6 15 1 2.5 Z" fill="var(--ink)"/></svg>021-555-0147</li>
      <li><svg viewBox="0 0 16 16"><path d="M4 1 L6 5 L4.5 6.5 Q6 10 9.5 11.5 L11 10 L15 12 L13.5 15 Q6 15 1 2.5 Z" fill="var(--ink)"/></svg>021-555-0147</li>
      <li><svg viewBox="0 0 16 16"><rect x="1" y="3" width="14" height="10" fill="var(--ink)"/><path d="M1 3 L8 9 L15 3" fill="none" stroke="#fff" stroke-width="1.5"/></svg>name@velunda.com</li>
      <li><svg viewBox="0 0 16 16"><circle cx="8" cy="8" r="6.5" fill="none" stroke="var(--ink)" stroke-width="1.5"/><path d="M1.5 8 H14.5 M8 1.5 V14.5" stroke="var(--ink)" stroke-width="1.2"/></svg>www.velunda.com</li>
    </ul>

    <div class="holder"><strong>Your Name,</strong><span>Title</span></div>
  </section>
</body>
</html>
```